Business Postcard Design for Personal Training Company

Need a postcard design for my company called "Copperleaf Studio" Colors are Navy Blue, Blue, Grey and White.

On the front I want there to be pictures and it to feature a box that says "Free Consultation + 50% off your first session!"

And somehow to feature the following phrases " Lose Weight. Gain Muscle."
"Customized Personal training using Q-Pulse, the latest technology in fitness. Reach your fitness goals in just two 25-min sessions per week"

Also want featured the following phrases (maybe on back):

"up to 18 times more effective than a conventional gym workout"

I need the back of the postcard to have all my business information:

Address: 287 Wendover Ln, Building D Suite 318, Costa Mesa CA 92631
Website: copperleaf-studio.example
Phone #: (949) 555-0137
E-mail: copperleafwellness@mailbox.example

I am going to upload my logo, before and after pictures and pictures of people training on the device. Feel free to use as many/or little photos as you want.

Target Market(s)

Wealthy Adults 40+ years old looking for a personal trainer

Industry/Entity Type

Personal Trainer

Colors
0455a3
85cae6
aaaaaa
ffffff

Requirements
Must have
• At least two of the before and after photos, and two or more photos of people working out on the device.

```html
<!DOCTYPE html>
<html lang="en">
<head>
<meta charset="utf-8">
<title>Copperleaf Studio Postcard</title>
<link rel="stylesheet" href="https://fonts.googleapis.com/css2?family=Archivo+Black&family=Oswald:wght@500;600&family=Lato:wght@400;700&family=Roboto:wght@700&display=swap">
<style>
  :root {
    --blue: #0aa3df;
    --navy: #0455a3;
    --sky: #85cae6;
    --grey: #aaaaaa;
    --grey-light: #d3d5d8;
    --ink: #3b3b3d;
    --white: #ffffff;
    --page: #e4e5e7;
  }
  html, body {
    margin: 0;
    width: 1200px;
    height: 1200px;
    overflow: hidden;
    background: var(--page);
  }
  .postcard {
    position: absolute;
    left: 250px;
    width: 700px;
    height: 543px;
    box-shadow: 0 6px 14px rgba(0,0,0,0.25);
    display: block;
  }
  .postcard--front { top: 36px; }
  .postcard--back { top: 621px; }
  .brand-name { font-family: "Lato", sans-serif; font-weight: 700; font-size: 19px; fill: var(--ink); letter-spacing: 0.5px; }
  .headline-lose { font-family: "Archivo Black", sans-serif; font-size: 86px; fill: var(--blue); }
  .headline-weight { font-family: "Archivo Black", sans-serif; font-size: 56px; fill: var(--blue); }
  .headline-gain { font-family: "Oswald", sans-serif; font-weight: 600; font-size: 56px; fill: var(--ink); }
  .body-copy { font-family: "Lato", sans-serif; font-size: 19px; fill: #222; }
  .offer-small { font-family: "Oswald", sans-serif; font-weight: 500; font-size: 19px; fill: var(--white); }
  .offer-big { font-family: "Oswald", sans-serif; font-weight: 600; font-size: 56px; fill: #111; }
  .effect-title { font-family: "Roboto", sans-serif; font-weight: 700; font-size: 38px; fill: var(--blue); }
  .effect-sub { font-family: "Roboto", sans-serif; font-weight: 700; font-size: 27px; fill: var(--ink); }
  .contact-bar-label { font-family: "Lato", sans-serif; font-weight: 700; font-size: 21px; fill: var(--white); }
  .contact-line { font-family: "Lato", sans-serif; font-size: 18px; fill: #222; }
  .session-label { font-family: "Lato", sans-serif; font-weight: 700; font-size: 16px; fill: var(--blue); }
</style>
</head>
<body>

<svg class="postcard postcard--front" viewBox="0 0 790 613" xmlns="http://www.w3.org/2000/svg">
  <defs>
    <clipPath id="front-clip"><rect width="790" height="613"/></clipPath>
    <clipPath id="front-photo-clip"><circle cx="568" cy="222" r="222"/></clipPath>
    <linearGradient id="front-panel" x1="0" y1="0" x2="1" y2="1">
      <stop offset="0" stop-color="#ffffff"/><stop offset="1" stop-color="#eceef0"/>
    </linearGradient>
    <linearGradient id="front-photo" x1="0" y1="0" x2="0" y2="1">
      <stop offset="0" stop-color="#c9cdd2"/><stop offset="0.45" stop-color="#6f7f74"/><stop offset="1" stop-color="#4f7a3c"/>
    </linearGradient>
    <radialGradient id="offer-fill" cx="0.5" cy="0.4" r="0.6">
      <stop offset="0" stop-color="#35bdf0"/><stop offset="1" stop-color="var(--blue)"/>
    </radialGradient>
  </defs>
  <g clip-path="url(#front-clip)">
    <rect class="card-bg" width="790" height="613" fill="#c3c5c8"/>
    <path class="panel-white" d="M0 0 H420 C400 220 520 470 760 560 C520 555 260 575 0 592 Z" fill="url(#front-panel)"/>
    <path class="swoosh-top" d="M255 0 C285 140 360 280 470 360" fill="none" stroke="var(--blue)" stroke-width="12"/>
    <path class="swoosh-top-thin" d="M280 0 C310 120 370 240 460 320" fill="none" stroke="var(--sky)" stroke-width="4"/>

    <circle class="photo-ring-outer" cx="568" cy="222" r="240" fill="#e3f3fb"/>
    <circle class="photo-ring" cx="568" cy="222" r="230" fill="var(--blue)"/>
    <g role="img" aria-label="Photo: client training outdoors in an electro-stimulation suit with a coach beside the device, harbour view behind">
      <rect clip-path="url(#front-photo-clip)" x="346" y="0" width="444" height="444" fill="url(#front-photo)"/>
    </g>

    <path class="band-grey" d="M0 566 C260 548 520 540 790 590 V613 H0 Z" fill="#c9cbce"/>
    <path class="band-blue" d="M0 580 C260 566 500 560 640 575 C700 582 750 598 790 606 V613 H0 Z" fill="var(--blue)"/>
    <path class="swoosh-bottom" d="M590 540 C660 560 730 580 790 585" fill="none" stroke="var(--blue)" stroke-width="14"/>
    <path class="swoosh-bottom-thin" d="M600 555 C680 575 740 595 790 600" fill="none" stroke="var(--white)" stroke-width="3"/>

    <g class="logo">
      <circle cx="46" cy="113" r="13" fill="var(--blue)"/>
      <text class="brand-name" x="66" y="120" textLength="196" lengthAdjust="spacingAndGlyphs">COPPERLEAF STUDIO</text>
    </g>

    <text class="headline-lose" x="38" y="300">LOSE</text>
    <text class="headline-weight" x="40" y="355">WEIGHT</text>
    <line x1="38" y1="368" x2="310" y2="368" stroke="var(--ink)" stroke-width="2"/>
    <text class="headline-gain" x="38" y="422" textLength="272" lengthAdjust="spacingAndGlyphs">GAIN MUSCLE</text>
    <line x1="38" y1="428" x2="310" y2="428" stroke="var(--ink)" stroke-width="2"/>

    <text class="body-copy">
      <tspan x="38" y="475">Customized Personal training using</tspan>
      <tspan x="38" y="499">Q-Pulse, the latest technology in fitness.</tspan>
      <tspan x="38" y="523">Reach your fitness goals in just two</tspan>
      <tspan x="38" y="547">25-min sessions per week</tspan>
    </text>

    <g class="offer-badge">
      <circle cx="538" cy="463" r="104" fill="#d7d9dc"/>
      <circle cx="538" cy="463" r="98" fill="#7e8286"/>
      <circle cx="538" cy="463" r="92" fill="var(--white)"/>
      <circle cx="538" cy="463" r="87" fill="url(#offer-fill)"/>
      <text class="offer-small" x="538" y="431" text-anchor="middle" textLength="140" lengthAdjust="spacingAndGlyphs">FREE CONSULTATION &amp;</text>
      <text class="offer-big" x="538" y="484" text-anchor="middle" textLength="146" lengthAdjust="spacingAndGlyphs">50% OFF</text>
      <text class="offer-small" x="538" y="504" text-anchor="middle" textLength="146" lengthAdjust="spacingAndGlyphs">YOUR FIRST SESSION!</text>
    </g>
  </g>
</svg>

<svg class="postcard postcard--back" viewBox="0 0 790 613" xmlns="http://www.w3.org/2000/svg">
  <defs>
    <clipPath id="back-clip"><rect width="790" height="613"/></clipPath>
    <clipPath id="back-photo-a"><circle cx="585" cy="150" r="128"/></clipPath>
    <clipPath id="back-photo-b"><circle cx="426" cy="440" r="94"/></clipPath>
    <clipPath id="back-photo-c"><circle cx="648" cy="440" r="104"/></clipPath>
    <linearGradient id="back-blue" x1="0" y1="0" x2="1" y2="1">
      <stop offset="0" stop-color="#2fb7ec"/><stop offset="1" stop-color="#1d8fd0"/>
    </linearGradient>
    <linearGradient id="back-top-photo" x1="0" y1="0" x2="0" y2="1">
      <stop offset="0" stop-color="#b9b4ae"/><stop offset="0.6" stop-color="#d9d6d2"/><stop offset="1" stop-color="#f2f2f2"/>
    </linearGradient>
    <linearGradient id="back-panel" x1="0" y1="0" x2="0" y2="1">
      <stop offset="0" stop-color="#ffffff"/><stop offset="1" stop-color="#e9ebed"/>
    </linearGradient>
  </defs>
  <g clip-path="url(#back-clip)">
    <rect class="card-bg" width="790" height="613" fill="url(#back-panel)"/>
    <path class="panel-blue" d="M372 0 C440 160 450 420 370 613 H790 V0 Z" fill="url(#back-blue)"/>
    <path class="panel-white-right" d="M470 0 C560 60 700 40 790 0 Z" fill="var(--white)"/>
    <path class="swoosh-grey" d="M440 330 C560 250 680 220 790 230 V260 C690 250 570 290 470 360 Z" fill="#c5c7ca"/>
    <path class="swoosh-white" d="M720 120 C750 100 770 90 790 85 V110 C770 115 750 125 730 140 Z" fill="var(--white)"/>
    <path class="swoosh-thin" d="M360 0 C420 160 430 420 350 613" fill="none" stroke="var(--white)" stroke-width="6"/>
    <path class="band-grey" d="M0 590 H380 V613 H0 Z" fill="#c9cbce"/>

    <g role="img" aria-label="Photo: coach guiding a client through an exercise in a training suit in the studio">
      <rect x="0" y="0" width="392" height="200" fill="url(#back-top-photo)"/>
    </g>

    <text class="effect-title" x="184" y="233" text-anchor="middle" textLength="306" lengthAdjust="spacingAndGlyphs">UP TO 18 TIMES</text>
    <text class="effect-title" x="184" y="273" text-anchor="middle" textLength="306" lengthAdjust="spacingAndGlyphs">MORE EFFECTIVE</text>
    <text class="effect-sub" x="184" y="307" text-anchor="middle">Than a conventional</text>
    <text class="effect-sub" x="184" y="335" text-anchor="middle">gym workout</text>

    <rect class="contact-bar" x="0" y="370" width="345" height="26" fill="var(--blue)"/>
    <text class="contact-bar-label" x="38" y="390">Contact Today</text>

    <g class="contact-icons" fill="var(--navy)">
      <path d="M28 422 c2 -2 4 -2 5 0 l2 3 c1 2 0 3 -1 4 c1 2 2 3 4 4 c1 -1 2 -2 4 -1 l3 2 c2 1 2 3 0 5 c-6 2 -17 -8 -17 -17 z"/>
      <path d="M27 454 h16 v11 h-16 z M27 454 l8 6 l8 -6" stroke="var(--white)" stroke-width="1.2"/>
      <circle cx="35" cy="487" r="8"/>
      <path d="M35 510 c-5 0 -8 4 -8 8 c0 6 8 14 8 14 c0 0 8 -8 8 -14 c0 -4 -3 -8 -8 -8 z"/>
      <circle cx="35" cy="518" r="3" fill="var(--white)"/>
    </g>
    <text class="contact-line" x="52" y="433">(949) 555-0137</text>
    <text class="contact-line" x="52" y="463" textLength="244" lengthAdjust="spacingAndGlyphs">copperleafwellness@mailbox.example</text>
    <text class="contact-line" x="52" y="493">copperleaf-studio.example</text>
    <text class="contact-line">
      <tspan x="52" y="524">287 Wendover Ln,</tspan>
      <tspan x="52" y="548">Building D Suite 318,</tspan>
      <tspan x="52" y="572">Costa Mesa CA 92631</tspan>
    </text>

    <g class="result-circle">
      <circle cx="585" cy="150" r="140" fill="#d6d8db"/>
      <circle cx="585" cy="150" r="134" fill="var(--blue)"/>
      <g role="img" aria-label="Before and after photos of a client: session 1 and session 30">
        <rect clip-path="url(#back-photo-a)" x="457" y="22" width="256" height="256" fill="#dcdcda"/>
        <line x1="585" y1="22" x2="585" y2="220" stroke="#bdbdbb" stroke-width="2"/>
      </g>
      <rect clip-path="url(#back-photo-a)" x="457" y="218" width="256" height="24" fill="rgba(255,255,255,0.9)"/>
      <text class="session-label" x="585" y="236" text-anchor="middle">session 1  |  session 30</text>
    </g>

    <g class="training-circle">
      <circle cx="426" cy="440" r="104" fill="#9a9da1"/>
      <circle cx="426" cy="440" r="97" fill="var(--white)"/>
      <g role="img" aria-label="Photo: client training on an exercise ball in the suit while the coach adjusts the device">
        <rect clip-path="url(#back-photo-b)" x="332" y="346" width="188" height="188" fill="#8e9bab"/>
      </g>
    </g>

    <g class="result-circle">
      <circle cx="648" cy="440" r="110" fill="var(--white)"/>
      <g role="img" aria-label="Before and after photos of a client: session 1 and session 20">
        <rect clip-path="url(#back-photo-c)" x="544" y="336" width="208" height="208" fill="#e2e3e4"/>
        <line x1="648" y1="336" x2="648" y2="500" stroke="#3a3a3a" stroke-width="4"/>
      </g>
      <rect clip-path="url(#back-photo-c)" x="544" y="480" width="208" height="24" fill="rgba(255,255,255,0.9)"/>
      <text class="session-label" x="648" y="498" text-anchor="middle">session 1  |  session 20</text>
    </g>
  </g>
</svg>

</body>
</html>
```